Business Card Design for a new Senior Concierge Business 1.3.24

I need a professional business card to handout at networking events for my senior helper business. I would like to use the logo I have uploaded. The design should be clear and easy to read and should list the following information...
Delia Parkhurst
Owner
www.HarborlightElderAides.com
Lakemont, Ohio
740.482.5079
Delia@harborlightelderaides.com

Target Market(s)

Senior Citizens

Industry/Entity Type

Personal Helper/ Assisstant

Contact Information for Business Card

I have included the details in the project description box.

Font styles to use
Serif

Colors
0054AA
0677BA
7BADD7
CADEEF
E8F1F8
59FF00
82FF00
B8FF75
E3FFCB
F4FFEA
E54698
E96AAD
F1A4CE
F9D9EA
FCEFF6
6B429C
8869AF
B7A5CE
E3DAEB
F3F0F8

Requirements
Must have
• Include uploaded logo
Nice to have
• The log that has been uploaded
Should not have
• No crazy fonts

```html
<!DOCTYPE html>
<html lang="en">
<head>
<meta charset="utf-8">
<title>Harborlight Elder Aides – Business Card</title>
<link rel="stylesheet" href="https://fonts.googleapis.com/css2?family=Lato:wght@400&family=Oswald:wght@700&family=Questrial&display=swap">
<style>
  :root {
    --backdrop: #3a3a3a;
    --card-white: #ffffff;
    --brand-violet: #652de9;
    --brand-teal: #008c93;
    --brand-crimson: #d81b5a;
    --text-light: #ffffff;
  }
  html, body {
    margin: 0;
    padding: 0;
    width: 1047px;
    height: 1200px;
    overflow: hidden;
    background: var(--backdrop);
  }
  .sheet {
    position: relative;
    width: 1047px;
    height: 1200px;
  }
  .card {
    position: absolute;
    left: 156px;
    width: 743px;
    height: 423px;
    border-radius: 20px;
    overflow: hidden;
    background: var(--card-white);
  }
  .card--front { top: 120px; }
  .card--back  { top: 634px; }

  .front-panel {
    position: absolute;
    inset: 0;
  }

  .wordmark {
    position: absolute;
    font-family: "Questrial", "Century Gothic", sans-serif;
    font-weight: 400;
    color: var(--brand-violet);
    line-height: 1;
    display: flex;
    align-items: center;
  }
  .wordmark__dot {
    border-radius: 50%;
    background: var(--brand-violet);
    flex: none;
  }
  .wordmark__name { display: flex; flex-direction: column; }

  .wordmark--front { left: 56px; top: 134px; gap: 12px; }
  .wordmark--front .wordmark__dot { width: 30px; height: 30px; }
  .wordmark--front .wordmark__line1 { font-size: 42px; }
  .wordmark--front .wordmark__line2 { font-size: 24px; margin-top: 4px; }

  .wordmark--back { right: 62px; top: 292px; gap: 18px; }
  .wordmark--back .wordmark__dot { width: 44px; height: 44px; }
  .wordmark--back .wordmark__line1 { font-size: 58px; }
  .wordmark--back .wordmark__line2 { font-size: 32px; margin-top: 4px; }

  .holder {
    position: absolute;
    right: 33px;
    top: 216px;
    text-align: right;
    color: var(--text-light);
  }
  .holder__name {
    font-family: "Oswald", "Impact", sans-serif;
    font-weight: 700;
    font-size: 37px;
    line-height: 1;
    letter-spacing: 0.3px;
    margin: 0;
  }
  .holder__role {
    font-family: "Lato", sans-serif;
    font-size: 20px;
    margin: 6px 0 0;
  }

  .contacts {
    position: absolute;
    right: 33px;
    top: 298px;
    margin: 0;
    padding: 0;
    list-style: none;
    font-family: "Lato", sans-serif;
    font-size: 18px;
    color: var(--text-light);
  }
  .contacts__item {
    display: flex;
    justify-content: flex-end;
    align-items: center;
    gap: 14px;
    height: 27px;
  }
  .contacts__item--phone { font-size: 20px; }
  .contacts__icon { width: 18px; height: 18px; flex: none; }
</style>
</head>
<body>
<main class="sheet">

  <section class="card card--front" aria-label="Card front">
    <svg class="front-panel" viewBox="0 0 743 423" width="743" height="423" aria-hidden="true">
      <polygon points="412,0 428,0 312,423 296,423" fill="var(--brand-teal)"/>
      <polygon points="440,0 743,0 743,423 324,423" fill="var(--brand-violet)"/>
      <rect x="0" y="415" width="296" height="8" fill="var(--brand-crimson)"/>
    </svg>

    <div class="wordmark wordmark--front">
      <span class="wordmark__dot"></span>
      <span class="wordmark__name">
        <span class="wordmark__line1">Harborlight</span>
        <span class="wordmark__line2">Elder Aides</span>
      </span>
    </div>

    <div class="holder">
      <h1 class="holder__name">DELIA PARKHURST</h1>
      <p class="holder__role">Owner</p>
    </div>

    <ul class="contacts">
      <li class="contacts__item contacts__item--phone">740.482.5079
        <svg class="contacts__icon" viewBox="0 0 24 24" aria-hidden="true"><path d="M6.6 10.8a15 15 0 0 0 6.6 6.6l2.2-2.2c.3-.3.7-.4 1-.2 1.1.4 2.3.6 3.6.6.6 0 1 .4 1 1V20c0 .6-.4 1-1 1A17 17 0 0 1 3 4c0-.6.4-1 1-1h3.5c.6 0 1 .4 1 1 0 1.3.2 2.5.6 3.6.1.3 0 .7-.2 1z" fill="#fff"/></svg>
      </li>
      <li class="contacts__item">Delia@harborlightelderaides.com
        <svg class="contacts__icon" viewBox="0 0 24 24" aria-hidden="true"><rect x="2" y="5" width="20" height="14" fill="#fff"/><path d="M2 5l10 8 10-8" fill="none" stroke="var(--brand-violet)" stroke-width="1.6"/></svg>
      </li>
      <li class="contacts__item">HarborlightElderAides.com
        <svg class="contacts__icon" viewBox="0 0 24 24" aria-hidden="true"><circle cx="12" cy="12" r="9.5" fill="none" stroke="#fff" stroke-width="2"/><ellipse cx="12" cy="12" rx="4" ry="9.5" fill="none" stroke="#fff" stroke-width="1.6"/><path d="M3 12h18" stroke="#fff" stroke-width="1.6"/></svg>
      </li>
      <li class="contacts__item">Lakemont, Ohio
        <svg class="contacts__icon" viewBox="0 0 24 24" aria-hidden="true"><path d="M12 2a7 7 0 0 0-7 7c0 5 7 13 7 13s7-8 7-13a7 7 0 0 0-7-7z" fill="#fff"/><circle cx="12" cy="9" r="2.6" fill="var(--brand-violet)"/></svg>
      </li>
    </ul>
  </section>

  <section class="card card--back" aria-label="Card back">
    <div class="wordmark wordmark--back">
      <span class="wordmark__dot"></span>
      <span class="wordmark__name">
        <span class="wordmark__line1">Harborlight</span>
        <span class="wordmark__line2">Elder Aides</span>
      </span>
    </div>
  </section>

</main>
</body>
</html>
```